Book Cover for a book on Quiet Ventures

I am self-publishing my book on Brindlecart and need a book cover made. Below are the details. See attached templates for size we need to use. I also attached a previous cover we had made that I liked. The problem with it was they were two boys helping each other but the book is about women. I'm open to your ideas on the cover though, but I wanted to show you a style I liked as an idea.
Front of Cover
Book Title: Quiet Ventures
Book Subtitle: Unvarnished Notes of a Woman Founder
Author Name: Lorna T. Pelham
Add on the Spine of Cover: Quiet Ventures and Lorna T. Pelham
Back of the Cover Text:
Quiet Ventures: Unvarnished Notes of a Woman Founder is an honest account of a business owner’s experience attempting to navigate the start-up community while also pursuing spiritual growth. Author Lorna Pelham defines a spiritual entrepreneur as “someone who runs an enterprise with the purpose of growing love rather than material gain.” This book discusses the three dimensions of Quiet Ventures:
1. The business is an integral part of the founder’s spiritual journey.
2. Employees working for the spiritual enterprise, whether they know it or not, encounter this company because it's part of their spiritual path.
3. The business itself has a life force of its own and its purpose is to further the kingdom of heaven on earth.
These three dimensions happen simultaneously and work together to produce the greatest possible result. However, this can feel confusing to a founder juggling these dimensions while also trying to manage and run a business. This is not a formulaic self-help book or roadmap. Rather, it is a compilation of personal reflections that often seem at odds with the traditional world of entrepreneurship.
Below the description add my picture (see attached for my picture)
Bio text:
Lorna Pelham founded Halvex with the vision of ushering in a life-long education system that shifts away from standardization to one that empowers people to live their purpose. In college, Lorna interned for Open Meadow, a women’s empowerment initiative where she recognized her passion for helping people find their voice. Lorna's 20-year journey has come full circle to empowering other female CEOs who are pursuing the path of Quiet Ventures.
NOTE: Please note that Brindlecart puts a bar code on the bottom right of the back cover as is noted on the attached template.
Size template is attached to the brief, here are the sizes typed out:
# Description Width (in) Height (in)
1 Full Cover 12.79 9.25
2 Front Cover 6 9
3 Safe Area 5.875 8.75
4 Bleed 0.125 0.125
5 Margin 0.125 0.125
6 Spine 0.54 9
7 Spine Safe Area 0.415 8.75
8 Spine Margin 0.062 0.062
9 Barcode Margin 0.25 0.25
Pre-publication checklist
BRINDLECART TIPS for the final cover:
1. Save as a PDF. Your cover must be a single PDF that includes the back cover, spine, and front cover as one image.
2. Flatten all transparencies. These can cause the file to print with missing or distorted content. Consult your software's documentation to learn how.
3. Embed your fonts. Consult your software's documentation to learn how.
4. Remove crop marks, color bars, template text. Crop marks are lines showing where pages should be trimmed. Color bars are strips with a series of patches used to ensure color balance during printing. Also, remove any template text, PDF creation guides, or software references.
5. Ensure your cover image meets the minimum resolution of 300 DPI (dots per inch).
6. Optimize PDFs. Optimization is useful to reduce your file size, allowing for higher performance when transferring, uploading, viewing, and printing the files.
7. Remove file security. Locked or encrypted files will fail review.
Target Market(s)
Women who want to be CEOs or are currently CEOs of companies.
Industry/Entity Type
Entrepreneurship, business, spirituality
Requirements
Must have
- Just the text on the description. A very welcoming feel.
Nice to have
- I like the idea of having a sunrise/sunset in the image somehow like in the example I attached to the brief, but again I'm open.
Should not have
- Please don't put any yoga or meditation poses or hands outstretched. I have a lot of interesting ones that look like my example so if you are going to submit after Saturday 10/29, please only do so if you have a new idea! Thanks!

```html
<!DOCTYPE html>
<html lang="en">
<head>
<meta charset="utf-8">
<title>Quiet Ventures – Full Cover</title>
<link rel="stylesheet" href="https://fonts.googleapis.com/css2?family=Oswald:wght@500;700&family=Tinos&display=swap">
<style>
  :root {
    --sky-top: #4c5f98;
    --sky-mid: #8a6f86;
    --sunset: #d9661f;
    --ember: #b4410f;
    --title-orange: #f6a417;
    --bright-yellow: #fff21a;
    --ink: #111111;
    --paper: #ffffff;
    --frame: #e9a12a;
  }
  html, body {
    margin: 0;
    padding: 0;
    width: 1200px;
    height: 860px;
    overflow: hidden;
    background: #222;
  }
  .cover {
    position: relative;
    width: 1200px;
    height: 860px;
    overflow: hidden;
    background: linear-gradient(180deg, var(--sky-top) 0%, var(--sky-mid) 32%, var(--sunset) 68%, var(--ember) 100%);
  }

  /* Back cover */
  .back-blurb {
    position: absolute;
    left: 45px;
    top: 56px;
    width: 485px;
    font-family: "Tinos", "Times New Roman", serif;
    font-size: 16.6px;
    line-height: 18.7px;
    color: var(--paper);
  }
  .back-blurb p { margin: 0 0 12px; }
  .dimensions {
    margin: 0 0 12px;
    padding: 0 0 0 25px;
    list-style: none;
  }
  .dimensions li { position: relative; }
  .dimensions li::before {
    content: "";
    position: absolute;
    left: -22px;
    top: 6px;
    width: 6px;
    height: 6px;
    border-radius: 50%;
    background: var(--title-orange);
  }

  .author-portrait {
    position: absolute;
    left: 38px;
    top: 475px;
    width: 211px;
    height: 221px;
    border: 1.5px solid var(--frame);
    background: linear-gradient(180deg, #7fb15a 0%, #5f9a44 45%, #c94f86 75%, #d6408a 100%);
  }
  .bracket {
    position: absolute;
    border-color: var(--frame);
    border-style: solid;
  }
  .bracket-top-left {
    left: 28px; top: 463px; width: 58px; height: 58px;
    border-width: 2px 0 0 2px;
  }
  .bracket-bottom-right {
    left: 487px; top: 646px; width: 57px; height: 57px;
    border-width: 0 2px 2px 0;
  }
  .author-bio {
    position: absolute;
    left: 271px;
    top: 474px;
    width: 262px;
    margin: 0;
    font-family: "Tinos", "Times New Roman", serif;
    font-size: 16.2px;
    line-height: 17.4px;
    color: var(--paper);
  }
  .barcode-area {
    position: absolute;
    left: 360px;
    top: 720px;
    width: 191px;
    height: 115px;
    background: var(--bright-yellow);
  }

  /* Spine */
  .spine-text {
    position: absolute;
    transform-origin: 0 0;
    transform: rotate(90deg);
    font-family: "Oswald", "Arial Narrow", sans-serif;
    font-weight: 700;
    font-size: 25px;
    letter-spacing: 0.3px;
    color: var(--paper);
    white-space: nowrap;
    line-height: 1;
    text-shadow: 0 0 3px rgba(0,0,0,0.35);
  }
  .spine-author { top: 64px; left: 613px; }
  .spine-title { top: 290px; left: 613px; }

  /* Front cover */
  .front-art {
    position: absolute;
    left: 660px;
    top: 190px;
    width: 520px;
    height: 520px;
    border-radius: 50%;
    background: radial-gradient(circle at 50% 60%, rgba(255,250,230,0.95) 0%, rgba(190,215,240,0.75) 30%, rgba(90,140,200,0.45) 55%, rgba(255,255,255,0) 72%);
  }
  .front-author {
    position: absolute;
    left: 636px;
    width: 564px;
    top: 100px;
    margin: 0;
    text-align: center;
    font-family: "Oswald", "Arial Narrow", sans-serif;
    font-weight: 700;
    font-size: 58px;
    line-height: 1;
    color: var(--title-orange);
  }
  .front-title {
    position: absolute;
    left: 640px;
    width: 560px;
    top: 336px;
    margin: 0;
    text-align: center;
    font-family: "Oswald", "Arial Narrow", sans-serif;
    font-weight: 700;
    color: var(--title-orange);
    text-transform: uppercase;
    text-shadow: 3px 4px 6px rgba(0,0,0,0.75);
  }
  .front-title .title-line { display: block; }
  .front-title .title-first { font-size: 118px; line-height: 112px; letter-spacing: 6px; }
  .front-title .title-second { font-size: 62px; line-height: 62px; letter-spacing: 3px; }
  .front-subtitle {
    position: absolute;
    left: 636px;
    width: 564px;
    top: 522px;
    margin: 0;
    text-align: center;
    font-family: "Oswald", "Arial Narrow", sans-serif;
    font-weight: 500;
    font-size: 25px;
    line-height: 30px;
    color: var(--ink);
    text-transform: uppercase;
  }
</style>
</head>
<body>
<main class="cover">

  <section class="back-cover">
    <div class="back-blurb">
      <p>QUIET VENTURES: Unvarnished Notes of a Woman Founder is an honest account of a business owner’s experience attempting to navigate the start-up community while also pursuing spiritual growth. Author Lorna Pelham defines a spiritual entrepreneur as “someone who runs an enterprise with the purpose of growing love rather than material gain.” This book discusses the three dimensions of Quiet Ventures:</p>
      <ul class="dimensions">
        <li>The business is an integral part of the founder’s spiritual journey.</li>
        <li>Employees working for the spiritual enterprise, whether they know it or not, encounter this company because it’s part of their spiritual path.</li>
        <li>The business itself has a life force of its own and its purpose is to further the kingdom of heaven on earth.</li>
      </ul>
      <p>These three dimensions happen simultaneously and work together to produce the greatest possible result. However, this can feel confusing to a founder juggling these dimensions while also trying to manage and run a business. This is not a formulaic self-help book or roadmap. Rather, it is a compilation of personal reflections that often seem at odds with the traditional world of entrepreneurship.</p>
    </div>

    <span class="bracket bracket-top-left"></span>
    <div class="author-portrait" role="img" aria-label="Portrait photo of the author outdoors"></div>
    <p class="author-bio">Lorna Pelham founded Halvex with the vision of ushering in a life-long education system that shifts away from standardization to one that empowers people to live their purpose. In college, Lorna interned for Open Meadow, a women’s empowerment initiative where she recognized her passion for helping people find their voice. Lorna’s 20-year journey has come full circle to empowering other female CEOs who are pursuing the path of Quiet Ventures.</p>
    <span class="bracket bracket-bottom-right"></span>

    <div class="barcode-area"></div>
  </section>

  <section class="spine">
    <span class="spine-text spine-author">LORNA T. PELHAM</span>
    <span class="spine-text spine-title">QUIET VENTURES</span>
  </section>

  <section class="front-cover">
    <div class="front-art" role="img" aria-label="Glowing globe wrapped in network lines over a sunset sky"></div>
    <h2 class="front-author">LORNA T. PELHAM</h2>
    <h1 class="front-title">
      <span class="title-line title-first">Quiet</span>
      <span class="title-line title-second">Ventures</span>
    </h1>
    <p class="front-subtitle">Unvarnished Notes of a Woman Founder</p>
  </section>

</main>
</body>
</html>
```